Custom unique Stationary design for Logistics company

We need a custom, unique , elegant and luxurious full stationary design using our new logo, following these guidelines:
1- Business card: double sided, both sides uses the navy blue as the background main color (same as the code of the navy blue used in our logo).
2- envelope and folder: also use the same navy blue as the main background color.
3- book cover( notepad cover) : same thing with the navy blue
4- letterhead: feel free to use the combination of the colors in our logo.
5- rest of the items are up to your creativity

Target Market(s)

corporates and other businesses

Industry/Entity Type

Logistics and heavy machines contractors

Requirements
Must have
• Letterhead, business card, envelope, notepad cover, paper, file
Nice to have
• navy blue to be main background color for business card, envelope, notepad cover

```html
<!DOCTYPE html>
<html lang="en">
<head>
<meta charset="utf-8">
<title>Northline Freight Stationery</title>
<link href="https://fonts.googleapis.com/css2?family=Montserrat:wght@500;700;800&family=Open+Sans:wght@400;600&family=Great+Vibes&display=swap" rel="stylesheet">
<style>
:root{
  --navy:#0f4f75;
  --orange:#e8572a;
  --paper:#ffffff;
  --ink:#33424f;
  --muted:#7a8894;
  --stage:#e4e5e7;
}
*{box-sizing:border-box;margin:0;padding:0}
html,body{width:1200px;height:4397px;overflow:hidden}
body{background:var(--stage);font-family:"Open Sans",Arial,sans-serif;color:var(--ink);position:relative}
.band{position:absolute;left:0;width:1200px;overflow:hidden}
.band--cards{top:0;height:840px;background:linear-gradient(#d9dadc,#bfc1c4)}
.band--letter{top:840px;height:870px;background:var(--stage)}
.band--envelope{top:1710px;height:780px;background:#e9e9ea}
.band--folder{top:2490px;height:1150px;background:var(--stage)}
.band--notepad{top:3640px;height:757px;background:#e6e7e8}
.sheet{position:absolute;overflow:hidden;box-shadow:0 14px 30px rgba(0,0,0,.22)}
.sheet svg.swoosh{position:absolute;inset:0;width:100%;height:100%}
.navy{background:var(--navy)}
.white{background:var(--paper)}
.brand{font-family:"Montserrat",Arial,sans-serif;font-weight:800;letter-spacing:.04em;display:flex;align-items:center;gap:10px;white-space:nowrap}
.brand__dot{width:12px;height:12px;border-radius:50%;background:var(--orange);flex:none}
.brand--light{color:#fff}
.brand--dark{color:var(--navy)}
.contact{font-size:12px;line-height:1.45}
.contact li{list-style:none;display:flex;align-items:center;gap:8px}
.icon{width:12px;height:12px;flex:none}
/* business card */
.card{width:520px;height:300px;top:270px}
.card--front{left:50px}
.card--back{left:630px}
.card--back .brand{position:absolute;left:0;right:0;top:130px;justify-content:center;font-size:30px}
.card--back::after{content:"";position:absolute;left:0;right:0;bottom:0;height:6px;background:var(--orange)}
.card__brand{position:absolute;right:24px;top:36px;font-size:20px}
.card__rule{position:absolute;left:200px;top:80px;width:130px;height:2px;background:var(--navy);opacity:.6}
.card__person{position:absolute;left:34px;top:92px}
.card__name{font-family:"Montserrat",sans-serif;font-weight:700;font-size:19px;color:var(--navy)}
.card__name span{color:var(--orange)}
.card__role{font-size:12px;margin:2px 0 8px}
/* letterhead */
.letter{left:330px;top:50px;width:540px;height:760px}
.letter__brand{position:absolute;left:44px;top:40px;font-size:22px}
.letter__rule{position:absolute;left:44px;right:44px;top:90px;height:2px;background:var(--navy);opacity:.6}
.letter__contact{position:absolute;right:44px;top:106px;width:130px;font-size:9px;line-height:1.6;text-align:right;color:var(--muted)}
.letter__body{position:absolute;left:44px;top:110px;width:300px;font-size:9px;line-height:1.55}
.letter__body p{margin-bottom:9px}
.signature{font-family:"Great Vibes",cursive;font-size:24px;color:var(--ink)}
/* envelope */
.envelope{left:250px;width:700px;height:330px}
.envelope--back{top:40px}
.envelope--back .brand{position:absolute;left:0;right:0;top:145px;justify-content:center;font-size:30px}
.envelope--front{top:410px}
.envelope__brand{position:absolute;left:40px;top:30px;font-size:20px}
.envelope__address{position:absolute;left:40px;top:62px;font-size:12px;line-height:1.5}
/* folder */
.folder{top:40px;width:380px;height:500px}
.folder--cover{left:220px}
.folder--cover .brand{position:absolute;left:40px;top:70px;font-size:19px}
.folder__contact{position:absolute;left:30px;bottom:28px;color:#fff;font-size:10px;line-height:1.7}
.folder__contact li{list-style:none}
.folder--flap{left:600px}
.folder--flap .brand{position:absolute;left:40px;top:70px;font-size:19px}
.folder-inside{top:600px;width:380px;height:500px}
.folder-inside--left{left:220px}
.folder-inside--right{left:600px}
.pocket{position:absolute;left:0;right:0;bottom:0;height:170px;background:var(--navy)}
.inner-letter{position:absolute;left:50px;top:30px;width:280px;height:360px;background:#fff;box-shadow:0 4px 12px rgba(0,0,0,.15);padding:26px 22px;font-size:7.5px;line-height:1.6}
.inner-letter .brand{font-size:14px;margin-bottom:18px}
.inner-letter p{margin-bottom:6px}
/* notepad */
.notepad{top:50px;width:420px;height:640px}
.notepad--cover{left:150px}
.notepad--cover .brand{position:absolute;left:0;right:0;top:300px;justify-content:center;font-size:24px}
.notepad--paper{left:630px}
.notepad__brand{position:absolute;left:40px;top:34px;font-size:16px}
.notepad__date{position:absolute;right:40px;top:70px;font-size:12px}
.notepad__lines{position:absolute;left:30px;right:30px;top:110px;height:460px;background:repeating-linear-gradient(to bottom,transparent 0 27px,#8b96a0 27px 28px)}
.notepad__foot{position:absolute;left:0;right:0;bottom:0;height:26px;background:var(--navy);border-top:3px solid var(--orange)}
</style>
</head>
<body>

<section class="band band--cards" aria-label="Business card">
  <article class="sheet card card--front white">
    <svg class="swoosh" viewBox="0 0 520 300" preserveAspectRatio="none" aria-hidden="true">
      <path d="M0 300 L0 296 Q360 276 520 130 L520 300 Z" fill="#0f4f75"/>
      <path d="M0 286 Q355 266 520 116" fill="none" stroke="#e8572a" stroke-width="4"/>
    </svg>
    <div class="brand brand--dark card__brand"><span class="brand__dot"></span>NORTHLINE FREIGHT</div>
    <div class="card__rule"></div>
    <div class="card__person">
      <div class="card__name"><span>DANA</span> WHITFIELD</div>
      <div class="card__role">Co-Founder</div>
      <ul class="contact">
        <li>120 Harbor Lane, Unit 4,</li>
        <li>Westbrook, ON K0A 1B0</li>
        <li><svg class="icon" viewBox="0 0 12 12"><path d="M2 1h3l1 3-2 1a7 7 0 0 0 3 3l1-2 3 1v3c-6 0-9-3-9-9z" fill="#0f4f75"/></svg>000 555 0142</li>
        <li><svg class="icon" viewBox="0 0 12 12"><rect x="1" y="2.5" width="10" height="7" fill="#0f4f75"/><path d="M1 3l5 4 5-4" stroke="#fff" fill="none"/></svg>hello@northlinefreight.com</li>
        <li><svg class="icon" viewBox="0 0 12 12"><circle cx="6" cy="6" r="5" fill="#0f4f75"/><path d="M1 6h10M6 1v10" stroke="#fff" stroke-width=".8"/></svg>www.northlinefreight.com</li>
      </ul>
    </div>
  </article>
  <article class="sheet card card--back navy">
    <div class="brand brand--light"><span class="brand__dot"></span>NORTHLINE FREIGHT</div>
  </article>
</section>

<section class="band band--letter" aria-label="Letterhead">
  <article class="sheet letter white">
    <svg class="swoosh" viewBox="0 0 540 760" preserveAspectRatio="none" aria-hidden="true">
      <path d="M0 610 Q180 730 540 735 L540 760 L0 760 Z" fill="#0f4f75"/>
      <path d="M0 590 Q190 715 540 720" fill="none" stroke="#e8572a" stroke-width="3"/>
    </svg>
    <div class="brand brand--dark letter__brand"><span class="brand__dot"></span>NORTHLINE FREIGHT</div>
    <div class="letter__rule"></div>
    <div class="letter__contact">120 Harbor Lane, Unit 4<br>Westbrook, ON K0A 1B0<br>000 555 0142<br>hello@northlinefreight.com<br>www.northlinefreight.com</div>
    <div class="letter__body">
      <p>January 03, 2020</p>
      <p>Client Name<br>Project Director<br>Site Office<br>City, Region</p>
      <p><strong>Dear Mr. Parker,</strong></p>
      <p>Thank you for choosing our team for your upcoming freight project. We have reviewed the schedule and prepared a plan for heavy equipment transport across all sites.</p>
      <p>Our crews will coordinate pickup, loading and delivery windows with your site managers. Each move is tracked from dispatch to arrival so you always know where your cargo stands.</p>
      <p>Please review the attached details and let us know if any changes are needed before the first shipment.</p>
      <p>Regards,</p>
      <div class="signature">Jordan Reyes</div>
    </div>
  </article>
</section>

<section class="band band--envelope" aria-label="Envelope">
  <article class="sheet envelope envelope--back navy">
    <div class="brand brand--light"><span class="brand__dot"></span>NORTHLINE FREIGHT</div>
  </article>
  <article class="sheet envelope envelope--front white">
    <svg class="swoosh" viewBox="0 0 700 330" preserveAspectRatio="none" aria-hidden="true">
      <path d="M0 125 Q350 255 700 240 L700 330 L0 330 Z" fill="#0f4f75"/>
      <path d="M0 110 Q350 240 700 225" fill="none" stroke="#e8572a" stroke-width="4"/>
    </svg>
    <div class="brand brand--dark envelope__brand"><span class="brand__dot"></span>NORTHLINE FREIGHT</div>
    <div class="envelope__address">120 Harbor Lane, Unit 4,<br>Westbrook, ON K0A 1B0</div>
  </article>
</section>

<section class="band band--folder" aria-label="Presentation folder">
  <article class="sheet folder folder--cover navy">
    <div class="brand brand--light"><span class="brand__dot"></span>NORTHLINE FREIGHT</div>
    <ul class="folder__contact">
      <li>120 Harbor Lane, Unit 4, Westbrook, ON K0A 1B0</li>
      <li>000 555 0142 · hello@northlinefreight.com</li>
      <li>www.northlinefreight.com</li>
    </ul>
  </article>
  <article class="sheet folder folder--flap white">
    <svg class="swoosh" viewBox="0 0 380 500" preserveAspectRatio="none" aria-hidden="true">
      <path d="M0 450 Q220 460 380 360 L380 500 L0 500 Z" fill="#0f4f75"/>
      <path d="M0 440 Q220 450 375 352" fill="none" stroke="#e8572a" stroke-width="3"/>
    </svg>
    <div class="brand brand--dark"><span class="brand__dot"></span>NORTHLINE FREIGHT</div>
  </article>
  <article class="sheet folder-inside folder-inside--left white">
    <svg class="swoosh" viewBox="0 0 380 500" preserveAspectRatio="none" aria-hidden="true">
      <path d="M0 370 L260 370 Q320 400 380 500 L0 500 Z" fill="#0f4f75"/>
    </svg>
  </article>
  <article class="sheet folder-inside folder-inside--right white">
    <div class="inner-letter">
      <div class="brand brand--dark"><span class="brand__dot"></span>NORTHLINE FREIGHT</div>
      <p>January 03, 2020</p>
      <p><strong>Dear Mr. Parker,</strong></p>
      <p>Thank you for choosing our team for your upcoming freight project.</p>
      <p>Regards,</p>
    </div>
    <div class="pocket"></div>
  </article>
</section>

<section class="band band--notepad" aria-label="Notepad">
  <article class="sheet notepad notepad--cover navy">
    <div class="brand brand--light"><span class="brand__dot"></span>NORTHLINE FREIGHT</div>
  </article>
  <article class="sheet notepad notepad--paper white">
    <div class="brand brand--dark notepad__brand"><span class="brand__dot"></span>NORTHLINE FREIGHT</div>
    <div class="notepad__date">Date:..........</div>
    <div class="notepad__lines"></div>
    <div class="notepad__foot"></div>
  </article>
</section>

</body>
</html>
```